Visitenkarten-Design für Boutique-Unternehmensberatung
Zielgruppe
Boutique Unternehmensberatung für die Chemische Industrie. Wir unterstützen Unternehmen, die Beziehung zu Ihren Händlern zu optimieren.
Vorläufige Website vertriebsbruecke-online.de kann ggf weitere Einblicke geben. Hinweis: Diese Website wurde bisher noch nicht professionell erstellt.
Aufgabenstellung
Die Visitenkarte sollte vertrauenserweckend und seriös wirken. Zeitgleich aber auch modern.

```html
<!DOCTYPE html>
<html lang="de">
<head>
<meta charset="utf-8">
<title>Visitenkarte Vertriebsbrücke</title>
<link rel="stylesheet" href="https://fonts.googleapis.com/css2?family=Montserrat:wght@400;500;700&display=swap">
<style>
  :root {
    --brand-blue: #0f5593;
    --paper: #ffffff;
    --backdrop: #cfd0d2;
    --ring: #f2f2f2;
    --photo-tone: linear-gradient(135deg, #c9a58c 0%, #9bb4c8 100%);
  }
  * { margin: 0; padding: 0; box-sizing: border-box; }
  html, body { width: 1200px; height: 852px; overflow: hidden; }
  body {
    background: var(--backdrop);
    font-family: "Montserrat", sans-serif;
    color: var(--brand-blue);
    position: relative;
  }
  .card {
    position: absolute;
    top: 258px;
    width: 520px;
    height: 336px;
    box-shadow: 0 6px 18px rgba(0,0,0,0.18);
    overflow: hidden;
  }
  .card-front { left: 50px; background: var(--brand-blue); }
  .card-back { left: 630px; background: var(--paper); }

  .brand {
    position: absolute;
    left: 50%; top: 50%;
    transform: translate(-50%, -50%);
    display: flex; align-items: center; gap: 14px;
    color: var(--paper);
  }
  .brand-dot { width: 40px; height: 40px; border-radius: 50%; background: var(--paper); }
  .brand-name { font-weight: 500; font-size: 26px; line-height: 1.05; }

  .band { position: absolute; left: 0; top: 0; }
  .portrait {
    position: absolute;
    left: 338px; top: 34px;
    width: 112px; height: 112px;
    border-radius: 50%;
    border: 6px solid var(--ring);
    background: var(--photo-tone);
  }
  .person-name {
    position: absolute; left: 28px; top: 78px;
    color: var(--paper); font-weight: 700; font-size: 30px; letter-spacing: 0.5px;
    white-space: nowrap;
  }
  .person-role { position: absolute; left: 34px; top: 130px; font-size: 17px; font-weight: 400; white-space: nowrap; }
  .contact-list { position: absolute; list-style: none; font-size: 12.5px; }
  .contact-list li { display: flex; align-items: center; gap: 8px; height: 22px; white-space: nowrap; }
  .contact-list svg { width: 14px; height: 14px; flex: none; }
  .contact-personal { left: 46px; top: 158px; }
  .contact-office { left: 300px; top: 170px; font-size: 10.5px; }
  .contact-office li { gap: 6px; }
  .contact-office svg { width: 13px; height: 13px; }
  .divider-v { position: absolute; left: 288px; top: 166px; width: 1.5px; height: 104px; background: var(--brand-blue); }
  .divider-h { position: absolute; left: 288px; top: 269px; width: 232px; height: 1.5px; background: var(--brand-blue); }
  .address { position: absolute; left: 50px; top: 250px; font-size: 12px; line-height: 1.65; font-style: normal; white-space: nowrap; }
  .address strong { font-weight: 700; }
</style>
</head>
<body>
  <section class="card card-front" aria-label="Vorderseite">
    <div class="brand">
      <span class="brand-dot"></span>
      <span class="brand-name">Vertriebs-<br>brücke</span>
    </div>
  </section>

  <section class="card card-back" aria-label="Rückseite">
    <svg class="band" width="520" height="336" viewBox="0 0 520 336" aria-hidden="true">
      <polygon points="0,0 520,0 520,26 420,26 330,124 0,124" fill="var(--brand-blue)"/>
    </svg>
    <div class="portrait" role="img" aria-label="Porträtfoto von Jonas Albrecht"></div>
    <h1 class="person-name">Jonas Albrecht</h1>
    <p class="person-role">Geschäftsführer / CEO</p>

    <ul class="contact-list contact-personal">
      <li><svg viewBox="0 0 14 14"><circle cx="7" cy="7" r="7" fill="var(--brand-blue)"/><path d="M4.5 3.5l1.5 0 .6 1.8-.9.7a5 5 0 0 0 2.3 2.3l.7-.9 1.8.6v1.5a1 1 0 0 1-1 1A6 6 0 0 1 3.5 4.5a1 1 0 0 1 1-1z" fill="#fff"/></svg>+49 69 / 12 34 56 78</li>
      <li><svg viewBox="0 0 14 14"><circle cx="7" cy="7" r="7" fill="var(--brand-blue)"/><rect x="3.5" y="4.5" width="7" height="5" fill="none" stroke="#fff" stroke-width="1"/><path d="M3.5 4.5l3.5 3 3.5-3" fill="none" stroke="#fff" stroke-width="1"/></svg>ja@vertriebsbruecke-online.de</li>
    </ul>

    <div class="divider-v"></div>
    <div class="divider-h"></div>
    <ul class="contact-list contact-office">
      <li><svg viewBox="0 0 14 14"><circle cx="7" cy="7" r="7" fill="var(--brand-blue)"/><path d="M4.5 3.5l1.5 0 .6 1.8-.9.7a5 5 0 0 0 2.3 2.3l.7-.9 1.8.6v1.5a1 1 0 0 1-1 1A6 6 0 0 1 3.5 4.5a1 1 0 0 1 1-1z" fill="#fff"/></svg>+49 69 / 12 34 56 78</li>
      <li><svg viewBox="0 0 14 14"><circle cx="7" cy="7" r="7" fill="var(--brand-blue)"/><rect x="3.5" y="4.5" width="7" height="5" fill="none" stroke="#fff" stroke-width="1"/><path d="M3.5 4.5l3.5 3 3.5-3" fill="none" stroke="#fff" stroke-width="1"/></svg>info@vertriebsbruecke-online.de</li>
      <li><svg viewBox="0 0 14 14"><circle cx="7" cy="7" r="7" fill="var(--brand-blue)"/><circle cx="7" cy="7" r="3.5" fill="none" stroke="#fff" stroke-width="0.9"/><ellipse cx="7" cy="7" rx="1.5" ry="3.5" fill="none" stroke="#fff" stroke-width="0.9"/><path d="M3.5 7h7" stroke="#fff" stroke-width="0.9"/></svg>www.vertriebsbruecke-online.de</li>
    </ul>

    <address class="address">
      <strong>JAV Vertriebsbrücke GmbH i.G.</strong><br>
      Lindenweg 12<br>
      60311 Frankfurt
    </address>
  </section>
</body>
</html>
```